Health Care Company with Logo Needs Business Cards designed

We are a luxury behavioral health company looking for business cards design we already have a logo and are looking for someone to design a sophisticated luxurious looking business card. Please note that Card design should be captivating just like the logo and also encompass the logo color

Industry/Entity Type

Healthcare

Contact Information for Business Card

Logo,company name, tagline, my name and title, contact details, and physical address

```html
<!DOCTYPE html>
<html lang="en">
<head>
<meta charset="utf-8">
<title>Willowmere Wellness – Business Cards</title>
<link href="https://fonts.googleapis.com/css2?family=Roboto+Condensed:wght@700&family=Roboto:ital,wght@0,400;0,500;1,400&display=swap" rel="stylesheet">
<style>
  :root {
    --backdrop: #2a2a2a;
    --card: #efefef;
    --purple: #733680;
    --blue: #0f93d2;
    --orange: #e48a1c;
    --ink: #3a3a3a;
    --white: #ffffff;
  }
  * { margin: 0; padding: 0; box-sizing: border-box; }
  html, body { width: 1200px; height: 1138px; overflow: hidden; background: var(--backdrop); }
  .canvas { position: relative; width: 1200px; height: 1138px; }

  .card {
    position: absolute;
    background: var(--card);
    border-radius: 14px;
    overflow: hidden;
  }
  .card-front { left: 274px; top: 186px; width: 623px; height: 376px; }
  .card-back  { left: 276px; top: 608px; width: 618px; height: 374px; }

  .brand-name {
    font-family: "Roboto", sans-serif;
    font-weight: 500;
    color: var(--purple);
    line-height: 1;
    white-space: nowrap;
  }
  .brand-tagline {
    font-family: "Roboto", sans-serif;
    font-weight: 400;
    color: var(--blue);
    letter-spacing: 2.4px;
    line-height: 1;
    white-space: nowrap;
  }

  .front-lockup {
    position: absolute; left: 0; right: 0; top: 158px;
    text-align: center;
  }
  .front-lockup .brand-name { font-size: 40px; }
  .front-lockup .brand-tagline { font-size: 12.5px; margin-top: 10px; }

  .back-mark {
    position: absolute; left: 42px; top: 42px;
    width: 78px; height: 78px; border-radius: 50%;
    background: var(--orange);
  }
  .back-lockup { position: absolute; left: 141px; top: 58px; }
  .back-lockup .brand-name { font-size: 38px; }
  .back-lockup .brand-tagline { font-size: 12px; margin-top: 9px; }

  .person { position: absolute; left: 40px; top: 190px; }
  .person-name {
    font-family: "Roboto Condensed", sans-serif; font-weight: 700;
    font-size: 24px; color: var(--purple); line-height: 1;
  }
  .person-title {
    font-family: "Roboto", sans-serif; font-style: italic;
    font-size: 15px; color: var(--ink); margin-top: 6px; margin-left: -4px;
  }

  .waves { position: absolute; left: 0; top: 0; }

  .contact {
    position: absolute; right: 34px; top: 259px;
    font-family: "Roboto", sans-serif; font-size: 14.5px; color: var(--white);
    text-align: right; list-style: none;
  }
  .contact li { display: flex; justify-content: flex-end; align-items: center; height: 22px; }
  .contact svg { margin-left: 14px; }
  .contact .address { margin-top: 4px; margin-right: -8px; }
</style>
</head>
<body>
<main class="canvas">

  <section class="card card-front" aria-label="Card front">
    <div class="front-lockup">
      <div class="brand-name">Willowmere Wellness</div>
      <div class="brand-tagline">COMPASSIONATE CARE FOR MIND AND SPIRIT</div>
    </div>
  </section>

  <section class="card card-back" aria-label="Card back">
    <svg class="waves" width="618" height="374" viewBox="0 0 618 374" aria-hidden="true">
      <path fill="var(--purple)" d="M0,332 C120,372 250,352 360,292 C450,242 520,202 618,196 L618,374 L0,374 Z"/>
      <path fill="var(--blue)" d="M618,156 C520,156 460,185 380,240 C300,290 180,315 50,300 C180,308 300,298 390,252 C470,208 540,178 618,170 Z"/>
      <path fill="var(--orange)" d="M0,288 C80,308 200,318 308,265 C210,312 100,324 0,318 Z"/>
    </svg>

    <div class="back-mark" aria-hidden="true"></div>
    <div class="back-lockup">
      <div class="brand-name">Willowmere Wellness</div>
      <div class="brand-tagline">COMPASSIONATE CARE FOR MIND AND SPIRIT</div>
    </div>

    <div class="person">
      <div class="person-name">MARCUS HALE</div>
      <div class="person-title">Managing Director</div>
    </div>

    <ul class="contact">
      <li>000-222-0000
        <svg width="14" height="12" viewBox="0 0 14 12" aria-hidden="true"><path fill="#fff" d="M1,4 C1,1 13,1 13,4 L10,5 L10,3.5 L4,3.5 L4,5 Z M3,6 L11,6 L12,11 L2,11 Z"/></svg>
      </li>
      <li>willowmerewellness.com
        <svg width="14" height="12" viewBox="0 0 14 12" aria-hidden="true"><rect x="0.5" y="1" width="13" height="10" fill="#fff"/><path d="M0.5,1 L7,7 L13.5,1" fill="none" stroke="var(--purple)" stroke-width="1.2"/></svg>
      </li>
      <li>hello@willowmere.com
        <svg width="14" height="14" viewBox="0 0 14 14" aria-hidden="true"><g fill="none" stroke="#fff" stroke-width="1.2"><circle cx="7" cy="7" r="6"/><ellipse cx="7" cy="7" rx="2.6" ry="6"/><path d="M1,7 H13 M2,4 H12 M2,10 H12"/></g></svg>
      </li>
      <li class="address">48, Elm Street, Any Town, US 654321</li>
    </ul>
  </section>

</main>
</body>
</html>
```